Website Design Project for Beauty & Wellness Professionals

As background information, I have a website that is focused on Beauty & Wellness Professionals:
- Job Search (www.lumarinovo.com)
- Business Classifieds (negocios.lumarinovo.com)
- Freelancer Classifieds (freelancer.lumarinovo.com)
- Course Reviews (cursos.lumarinovo.com)

All those websites use standard templates.

I need a DESIGN for the HOME PAGE (no coding) of the Website Platform that consolidates the four platforms under the same design.

Website designs that we like:
- quelvox.com
- brintmoor.com

Target Market(s)

Brazilian Professionals from Beauty & Wellness sector

Industry/Entity Type

Business

Requirements
Must have
• Website designs that we like:
- quelvox.com
- brintmoor.com

```html
<!DOCTYPE html>
<html lang="pt-BR">
<head>
<meta charset="utf-8">
<title>Lumarinovo Beauty — Vagas de Emprego</title>
<link href="https://fonts.googleapis.com/css2?family=Arimo:wght@400;700&family=Open+Sans:wght@400;600;700&family=Cabin+Condensed:wght@400&display=swap" rel="stylesheet">
<style>
:root{
  --teal:#1e6e8c;
  --teal-dark:#17506a;
  --teal-btn:#2b8bb0;
  --orange:#c9643a;
  --orange-dark:#b2522b;
  --green:#8dc680;
  --green-line:#5e9a54;
  --brown:#5c2413;
  --text:#222;
  --line:#bdbdbd;
  --grey-box:#ececec;
  --skin-light:#f3d9cc;
  --skin:#e2b19c;
  --skin-deep:#b87a62;
  --hair:#3a2420;
  --hair-dark:#1c1214;
  --lilac:#c58fb4;
  --magenta:#a3306f;
  --lip:#b8283a;
}
*{box-sizing:border-box;margin:0;padding:0}
html,body{width:1200px;height:2503px;overflow:hidden;background:#fff}
body{position:relative;font-family:"Open Sans",Arial,sans-serif;color:var(--text)}
.topline{position:absolute;left:0;top:0;width:1200px;height:8px;background:#a9d7ea}
.brand{position:absolute;left:142px;top:26px;display:flex;flex-direction:column;align-items:flex-start;gap:8px}
.brand-dot{width:62px;height:62px;border-radius:50%;background:var(--teal);margin-left:42px}
.brand-name{font-family:"Cabin Condensed",Arial,sans-serif;font-size:29px;color:var(--teal);line-height:1}
.top-actions{position:absolute;left:661px;top:63px;display:flex;gap:9px}
.top-btn{width:195px;height:37px;background:linear-gradient(#3499bf,#1f7aa0);color:#fff;font:700 11.5px Arimo,Arial,sans-serif;display:flex;align-items:center;justify-content:center}
.main-nav{position:absolute;left:140px;top:154px;width:920px;height:53px;background:linear-gradient(#dc7a4c,var(--orange-dark));display:flex;align-items:center;justify-content:space-between;padding:0 10px;border-bottom:3px solid #e9c2ad}
.main-nav a{color:#fff;text-decoration:none;font:400 12.5px Arimo,Arial,sans-serif}

.hero{position:absolute;left:140px;top:227px;width:920px;height:387px;
  background:
    radial-gradient(ellipse 34% 42% at 42% 60%,rgba(240,204,188,.95),rgba(226,174,154,.6) 55%,transparent 100%),
    radial-gradient(ellipse 28% 30% at 22% 18%,rgba(232,190,176,.9),transparent 100%),
    radial-gradient(ellipse 26% 30% at 82% 88%,rgba(176,52,130,.95),rgba(140,40,110,.5) 60%,transparent 100%),
    radial-gradient(ellipse 18% 22% at 90% 12%,rgba(214,150,196,.7),transparent 100%),
    radial-gradient(ellipse 16% 20% at 64% 10%,rgba(190,160,150,.55),transparent 100%),
    linear-gradient(100deg,#4a2a2a 0%,#6b4036 30%,var(--hair) 58%,var(--hair-dark) 100%)}
.hero-panel{position:absolute;left:588px;top:112px;width:332px;height:228px;background:rgba(26,16,20,.55);padding:20px 0 0 16px;color:#fff}
.hero-title{font:400 20px Arimo,Arial,sans-serif;letter-spacing:.5px}
.hero-sub{font:700 17px Arimo,Arial,sans-serif;color:#38c938;margin-top:12px}
.hero-search{display:flex;margin:14px 0 0 -10px}
.hero-input{width:218px;height:29px;background:#fff;color:var(--teal-dark);font:700 9.5px Arimo,Arial,sans-serif;display:flex;align-items:center;padding-left:10px}
.hero-go{width:102px;height:29px;background:var(--teal-btn);font:700 10px Arimo,Arial,sans-serif;display:flex;align-items:center;justify-content:center}
.hero-hint{font:400 11px Arimo,Arial,sans-serif;line-height:20px;margin-top:7px}

.section-title{position:absolute;font:700 15px Arimo,Arial,sans-serif;color:var(--teal-dark)}
.jobs{position:absolute;left:140px;top:681px;display:grid;grid-template-columns:repeat(3,193px);grid-auto-rows:224px;column-gap:12px}
.job-photo{height:114px;border:1px solid #d4d4d4}
.p1{background:radial-gradient(ellipse 40% 60% at 50% 45%,var(--skin-light),transparent),radial-gradient(ellipse 30% 60% at 50% 95%,#5a3a30,transparent),linear-gradient(90deg,#fbf7f4,#6e4536 45%,#6e4536 55%,#fbf7f4)}
.p2{background:radial-gradient(ellipse 45% 65% at 60% 55%,#8a5640,transparent),linear-gradient(120deg,#e5553a 0%,#d86a4a 40%,#f4ede8 75%)}
.p3{background:radial-gradient(ellipse 55% 60% at 35% 55%,var(--skin-light),transparent),radial-gradient(ellipse 20% 25% at 40% 45%,rgba(170,120,140,.6),transparent),linear-gradient(135deg,#f6ebe5,var(--skin) 80%)}
.p4{background:radial-gradient(ellipse 30% 70% at 65% 50%,#2e221e,transparent),radial-gradient(ellipse 40% 60% at 30% 50%,var(--skin),transparent),linear-gradient(90deg,#d9b98f,#b99066)}
.p5{background:radial-gradient(ellipse 50% 55% at 40% 50%,#f7e2da,transparent),radial-gradient(ellipse 20% 18% at 42% 72%,rgba(210,80,120,.6),transparent),linear-gradient(135deg,#f3d0c6,#e8aa9c)}
.p6{background:radial-gradient(ellipse 22% 45% at 52% 55%,var(--skin),transparent),radial-gradient(ellipse 25% 30% at 52% 20%,var(--hair),transparent),linear-gradient(90deg,#fdfbfa,#f2ebe8)}
.p7{background:radial-gradient(ellipse 50% 60% at 45% 50%,var(--skin-light),transparent),radial-gradient(ellipse 30% 60% at 15% 40%,#d9a66a,transparent),linear-gradient(135deg,#f4e7df,#d6a286)}
.p8{background:radial-gradient(ellipse 35% 55% at 50% 50%,#e8c0b0,transparent),radial-gradient(ellipse 18% 15% at 50% 78%,#8e2a6e,transparent),linear-gradient(135deg,#1f5f78,#3a6f8a 45%,#8a3a5e)}
.p9{background:radial-gradient(ellipse 40% 40% at 45% 55%,#e6b7a3,transparent),radial-gradient(ellipse 15% 12% at 40% 60%,var(--lip),transparent),linear-gradient(135deg,#2a1414,#5c2020 60%,#aa3232)}
.p10{background:radial-gradient(ellipse 35% 45% at 20% 30%,#e07898,transparent),radial-gradient(ellipse 45% 60% at 60% 55%,var(--skin-light),transparent),linear-gradient(135deg,#e8c7a6,#c98e6a)}
.p11{background:radial-gradient(ellipse 45% 60% at 55% 50%,var(--skin-light),transparent),radial-gradient(ellipse 30% 60% at 85% 40%,#2a1c18,transparent),linear-gradient(135deg,#d9d3cf,#8e7870)}
.p12{background:radial-gradient(ellipse 45% 55% at 40% 60%,#f2ddd4,transparent),radial-gradient(ellipse 35% 70% at 85% 30%,#4a2a22,transparent),linear-gradient(135deg,#fbf6f3,#d6b2a0)}
.p13{background:radial-gradient(ellipse 40% 60% at 50% 50%,#f6e3db,transparent),radial-gradient(ellipse 12% 10% at 50% 80%,var(--lip),transparent),radial-gradient(ellipse 30% 40% at 50% 5%,#6e4a3a,transparent),linear-gradient(#fff,#f3ece8)}
.p14{background:radial-gradient(ellipse 30% 50% at 65% 45%,var(--skin),transparent),radial-gradient(ellipse 25% 30% at 70% 12%,#7a4e3a,transparent),linear-gradient(90deg,#f1ebe6,#ddd4cf)}
.p15{background:radial-gradient(ellipse 40% 55% at 50% 55%,var(--skin-light),transparent),radial-gradient(ellipse 45% 80% at 20% 40%,#d8aa6a,transparent),linear-gradient(135deg,#e7c48d,#c0945e)}
.job-name{font:700 11px Arimo,Arial,sans-serif;color:var(--teal-dark);line-height:20px;margin:10px 0 0 3px}
.job-rule{width:152px;border-top:1px solid var(--line);margin:6px 0 0 3px}
.job-date{font:400 11px Arimo,Arial,sans-serif;margin:10px 0 0 3px}
.pager{position:absolute;left:425px;top:1804px;display:flex;gap:9px}
.pager span{width:23px;height:22px;border:1px solid #444;font:400 11px Arimo,Arial,sans-serif;display:flex;align-items:center;justify-content:center}

.ad{position:absolute;border:1px solid #ccc}
.ad-wide{left:140px;top:1866px;width:600px;height:102px;background:
  radial-gradient(ellipse 14% 40% at 10% 55%,#4caf50,transparent),
  radial-gradient(ellipse 12% 90% at 36% 100%,#c8322c,transparent),
  radial-gradient(ellipse 12% 90% at 44% 100%,#e8b020,transparent),
  linear-gradient(90deg,#eaf4e6,#ffffff 25%,#fbf3d8 50%,#ffffff 65%,#f4f8ec)}
.ad-side{left:774px;top:1788px;width:286px;height:180px;background:
  radial-gradient(ellipse 30% 45% at 75% 55%,#c3262e,transparent),
  radial-gradient(ellipse 30% 50% at 25% 60%,#6a6a74,transparent),
  linear-gradient(135deg,#f6f6f6,#eadede)}
.subscribe{position:absolute;left:774px;top:658px;width:286px;height:178px;background:var(--green);padding:16px 0 0 32px}
.subscribe h3{font:700 12.5px Arimo,Arial,sans-serif;color:#1c1c1c;padding-bottom:8px;border-bottom:1px solid var(--green-line);width:220px}
.subscribe p{font:400 10.5px Arimo,Arial,sans-serif;color:var(--teal-dark);line-height:19px;margin-top:9px}
.subscribe-input{width:220px;height:30px;background:#eee;font:400 8.5px Arimo,Arial,sans-serif;display:flex;align-items:center;padding-left:6px;margin-top:16px}
.subscribe-btn{width:102px;height:28px;background:linear-gradient(#666,#2d2d2d);color:#fff;font:700 9.5px Arimo,Arial,sans-serif;display:flex;align-items:center;justify-content:center;margin:5px 0 0 118px}
.categories{position:absolute;left:776px;top:882px}
.categories h3{font:700 14px Arimo,Arial,sans-serif;color:var(--teal-dark);width:204px;padding-bottom:6px;border-bottom:3px solid var(--teal-dark)}
.categories ul{list-style:none;width:185px}
.categories li{height:37.5px;display:flex;align-items:center;font:400 9.5px Arimo,Arial,sans-serif;border-bottom:2px solid var(--line)}
.tabs{position:absolute;left:776px;top:1584px;display:flex;gap:2px}
.tab{width:100px;height:28px;color:#fff;font:700 9.5px Arimo,Arial,sans-serif;display:flex;align-items:center;justify-content:center}
.tab-on{background:var(--orange)}
.tab-off{background:var(--teal);width:102px}
.tab-panel{position:absolute;left:776px;top:1612px;width:284px;height:157px;background:var(--grey-box);border:1px solid #ddd;padding:4px 0 0 22px}
.tab-panel li{list-style:none;width:185px;height:37.5px;display:flex;align-items:center;font:400 9.5px Arimo,Arial,sans-serif;border-bottom:1px solid var(--line)}

.feature{position:absolute;top:1992px;width:289px}
.feature h3{font:700 15px Arimo,Arial,sans-serif;color:var(--teal-dark);height:33px;border-bottom:4px solid var(--teal-dark)}
.feature-photo{height:138px;margin-top:23px;border:1px solid #ddd}
.f1{background:radial-gradient(ellipse 35% 55% at 45% 55%,var(--skin-light),transparent),radial-gradient(ellipse 35% 40% at 40% 10%,#e3c48e,transparent),radial-gradient(ellipse 25% 60% at 90% 40%,var(--skin-deep),transparent),linear-gradient(135deg,#fbf7f3,#e9d6c8)}
.f2{background:radial-gradient(ellipse 20% 55% at 45% 50%,#f0d6c8,transparent),radial-gradient(ellipse 60% 30% at 50% 5%,#5d7a5a,transparent),radial-gradient(ellipse 40% 25% at 50% 100%,#4a4a4a,transparent),linear-gradient(#e4ece6,#f6f3f0)}
.f3{background:radial-gradient(ellipse 40% 60% at 70% 50%,var(--skin-light),transparent),radial-gradient(ellipse 18% 25% at 40% 35%,#3a2a28,transparent),linear-gradient(135deg,#f5ecef,#dcb8c4)}
.feature h4{font:700 11px Arimo,Arial,sans-serif;color:var(--orange-dark);margin-top:25px}
.feature p{font:400 11px Arimo,Arial,sans-serif;line-height:24px;margin-top:8px}
.feature-btn{width:120px;height:31px;background:linear-gradient(#6d6d6d,#333);color:#fff;font:400 11.5px Arimo,Arial,sans-serif;display:flex;align-items:center;justify-content:center;margin-top:14px}

.site-footer{position:absolute;left:0;top:2387px;width:1200px;height:116px;background:var(--brown);color:#fff}
.footer-links{position:absolute;left:142px;top:30px;font:400 10px Arimo,Arial,sans-serif;word-spacing:1px}
.footer-copy{position:absolute;left:142px;top:62px;font:400 10.5px Arimo,Arial,sans-serif}
.social{position:absolute;left:936px;top:42px;display:flex;gap:8px}
.social span{width:25px;height:25px;border-radius:50%;border:2px solid #fff}
.s-a{background:#3b5b9a}.s-b{background:#3fa8dc}.s-c{background:#1c86b5}.s-d{background:#e8902a}
</style>
</head>
<body>
<div class="topline"></div>

<header>
  <div class="brand"><span class="brand-dot"></span><span class="brand-name">Lumarinovo Beauty</span></div>
  <div class="top-actions">
    <span class="top-btn">ANUNCIE VAGS EMPREGO</span>
    <span class="top-btn">ENTRAR/CADASTE -SE</span>
  </div>
  <nav class="main-nav">
    <a>HOME</a><a>BLOG</a><a>PARA PROFISSIONAIS</a><a>PARA EMPRESAS</a><a>EVENTOS&amp;PARCEIROS</a><a>SOBRE NOS</a><a>FALE CONOSCO</a>
  </nav>
</header>

<section class="hero" role="img" aria-label="Foto de maquiadora aplicando sombra nos olhos de uma modelo, com paletas de cores e flores lilás">
  <div class="hero-panel">
    <div class="hero-title">LUMARINOVO BEAUTY</div>
    <div class="hero-sub">Vagas de Emprego em Destaque</div>
    <div class="hero-search"><span class="hero-input">ESCREVA AQUI &nbsp;PROFISSAO E LOCAL</span><span class="hero-go">SEARCH</span></div>
    <div class="hero-hint">Busque Profissão e Local Desejados! Ex: Manicure<br>São Paulo; Cabeleireiro Rio de Janeiro</div>
  </div>
</section>

<h2 class="section-title" style="left:142px;top:640px">VAGAS DE EMPREGO EM DESTAQUS</h2>

<main class="jobs">
  <article><div class="job-photo p1" role="img" aria-label="Foto de modelo com pincéis de maquiagem"></div><div class="job-name">Mariana Teles/Salão Íris<br>Mariana Teles</div><div class="job-rule"></div><div class="job-date">July 24,2013</div></article>
  <article><div class="job-photo p2" role="img" aria-label="Foto de modelo sorrindo"></div><div class="job-name">Mariana Teles/Salão Íris<br>Mariana Teles</div><div class="job-rule"></div><div class="job-date">July 24,2013</div></article>
  <article><div class="job-photo p3" role="img" aria-label="Foto de maquiagem nos olhos"></div><div class="job-name">Mariana Teles/Salão Íris<br>Mariana Teles</div><div class="job-rule"></div><div class="job-date">July 24,2013</div></article>
  <article><div class="job-photo p4" role="img" aria-label="Foto de modelo segurando pincéis"></div><div class="job-name">Mariana Teles/Salão Íris<br>Mariana Teles</div><div class="job-rule"></div><div class="job-date">July 24,2013</div></article>
  <article><div class="job-photo p5" role="img" aria-label="Foto de cuidados com a pele"></div><div class="job-name">Mariana Teles/Salão Íris<br>Mariana Teles</div><div class="job-rule"></div><div class="job-date">July 24,2013</div></article>
  <article><div class="job-photo p6" role="img" aria-label="Foto de modelo aplicando pó"></div><div class="job-name">Mariana Teles/Salão Íris<br>Mariana Teles</div><div class="job-rule"></div><div class="job-date">July 24,2013</div></article>
  <article><div class="job-photo p7" role="img" aria-label="Foto de modelo com cílios marcados"></div><div class="job-name">Mariana Teles/Salão Íris<br>Mariana Teles</div><div class="job-rule"></div><div class="job-date">July 24,2013</div></article>
  <article><div class="job-photo p8" role="img" aria-label="Foto de maquiagem artística colorida"></div><div class="job-name">Mariana Teles/Salão Íris<br>Mariana Teles</div><div class="job-rule"></div><div class="job-date">July 24,2013</div></article>
  <article><div class="job-photo p9" role="img" aria-label="Foto de batom vermelho"></div><div class="job-name">Mariana Teles/Salão Íris<br>Mariana Teles</div><div class="job-rule"></div><div class="job-date">July 24,2013</div></article>
  <article><div class="job-photo p10" role="img" aria-label="Foto de modelo com flor no cabelo"></div><div class="job-name">Mariana Teles/Salão Íris<br>Mariana Teles</div><div class="job-rule"></div><div class="job-date">July 24,2013</div></article>
  <article><div class="job-photo p11" role="img" aria-label="Foto de aplicação de delineador"></div><div class="job-name">Mariana Teles/Salão Íris<br>Mariana Teles</div><div class="job-rule"></div><div class="job-date">July 24,2013</div></article>
  <article><div class="job-photo p12" role="img" aria-label="Foto de maquiagem com pincel fino"></div><div class="job-name">Mariana Teles/Salão Íris<br>Mariana Teles</div><div class="job-rule"></div><div class="job-date">July 24,2013</div></article>
  <article><div class="job-photo p13" role="img" aria-label="Foto de retrato de beleza com batom vermelho"></div><div class="job-name">Mariana Teles/Salão Íris<br>Mariana Teles</div><div class="job-rule"></div><div class="job-date">July 24,2013</div></article>
  <article><div class="job-photo p14" role="img" aria-label="Foto de modelo se maquiando diante do espelho"></div><div class="job-name">Mariana Teles/Salão Íris<br>Mariana Teles</div><div class="job-rule"></div><div class="job-date">July 24,2013</div></article>
  <article><div class="job-photo p15" role="img" aria-label="Foto de modelo loira"></div><div class="job-name">Mariana Teles/Salão Íris<br>Mariana Teles</div><div class="job-rule"></div><div class="job-date">July 24,2013</div></article>
</main>

<nav class="pager"><span>&lt;</span><span>1</span><span>2</span><span>3</span><span>4</span><span>5</span><span>6</span><span>7</span><span>8</span><span>&gt;</span></nav>

<div class="ad ad-wide" role="img" aria-label="Banner publicitário de evento de ciclismo"></div>

<aside>
  <div class="subscribe">
    <h3>ASSIN AR POR EMAIL</h3>
    <p>Mariana Teles/Salão Íris<br>Mariana Teles</p>
    <div class="subscribe-input">ASSIN AR POR EMAIL</div>
    <div class="subscribe-btn">SUBSCRIBE</div>
  </div>

  <div class="categories">
    <h3>VAGAS DE EMPREGO</h3>
    <ul>
      <li>AUXILIAR CABELEIREIRO</li><li>AUXILIAR LIMPEZA</li><li>CABELEIREIRO</li><li>DEPILADORA</li><li>DESIGNER SOBRANCELHA</li><li>DESTAQUE</li><li>ENFERMEIRA</li><li>ESTETICISTA</li><li>FISIOTERAPEUTA</li><li>GERÊNCIA/COORDENAÇÃO</li><li>MANICURE E PEDICURE</li><li>MAQUIADOR</li><li>MASSOTERAPEUTA</li><li>OUTROS</li><li>PODÓLOGO</li><li>RECEPÇÃO/ATENDIMENTO</li><li>VENDAS COSMÉTICOS</li>
    </ul>
  </div>

  <div class="tabs"><span class="tab tab-on">BUSCARPOR</span><span class="tab tab-off">TAGS</span></div>
  <ul class="tab-panel">
    <li>TIPO DE VAGA DE EMPREGO</li><li>SALÁRIO DA VAGA</li><li>CATEGORIA DA VAGA</li><li>DATA DE PUBLICAÇÃO</li>
  </ul>

  <div class="ad ad-side" role="img" aria-label="Anúncio de serviço de criação de sites com equipe e etiqueta de preço"></div>
</aside>

<section class="feature" style="left:140px">
  <h3>BUSCARPOR</h3>
  <div class="feature-photo f1" role="img" aria-label="Foto de maquiadora trabalhando em cliente"></div>
  <h4>BUSCARPOR</h4>
  <p>"Sed ut perspiciatis unde omnis iste natus error sit voluptatem accusantium doloremque laudantium, totam rem aperiam, eaque ipsa quae ab illo invent.</p>
  <div class="feature-btn">Experment Gratis</div>
</section>
<section class="feature" style="left:454px">
  <h3>BUSCARPOR</h3>
  <div class="feature-photo f2" role="img" aria-label="Foto de mulher se maquiando diante do espelho"></div>
  <h4>BUSCARPOR</h4>
  <p>"Sed ut perspiciatis unde omnis iste natus error sit voluptatem accusantium doloremque laudantium, totam rem aperiam, eaque ipsa quae ab illo invent.</p>
  <div class="feature-btn">Experment Gratis</div>
</section>
<section class="feature" style="left:771px">
  <h3>BUSCARPOR</h3>
  <div class="feature-photo f3" role="img" aria-label="Foto de aplicação de blush com pincel"></div>
  <h4>BUSCARPOR</h4>
  <p>"Sed ut perspiciatis unde omnis iste natus error sit voluptatem accusantium doloremque laudantium, totam rem aperiam, eaque ipsa quae ab illo invent.</p>
  <div class="feature-btn">Experment Gratis</div>
</section>

<footer class="site-footer">
  <div class="footer-links">HOME &nbsp;| &nbsp;BLOG &nbsp;| &nbsp;PARA PROFISSIONAIS &nbsp;| &nbsp;PARA EMPRESAS &nbsp;| &nbsp;EVENTOS&amp;PARCEIROS &nbsp;| &nbsp;SOBRE NOS &nbsp;| &nbsp;FALE CONOSCO</div>
  <div class="footer-copy">Copyrights @ 2013 All Rights Reserved</div>
  <div class="social"><span class="s-a"></span><span class="s-b"></span><span class="s-c"></span><span class="s-d"></span></div>
</footer>
</body>
</html>
```